TA BRAMLEY BUSINESS CARD DESIGN PROJECT

We need to utilize our logo that was expertly created on PixelHarbor and now need to match this with a business card design.

```html
<!DOCTYPE html>
<html lang="en">
<head>
<meta charset="UTF-8">
<title>TA Bramley Business Card</title>
<link href="https://fonts.googleapis.com/css2?family=Montserrat:wght@500;700;800&family=Open+Sans:wght@400&display=swap" rel="stylesheet">
<style>
  :root {
    --page-bg: #ebe6de;
    --card-dark: #161616;
    --brand-blue: #0f57ab;
    --text-light: #ffffff;
  }
  html, body {
    margin: 0;
    padding: 0;
    width: 1200px;
    height: 900px;
    overflow: hidden;
    background: var(--page-bg);
  }
  .canvas {
    position: relative;
    width: 1200px;
    height: 900px;
  }
  .card {
    position: absolute;
    left: 310px;
    width: 582px;
    height: 332px;
    border-radius: 27px;
    overflow: hidden;
  }
  .card-front {
    top: 86px;
    background: var(--card-dark);
  }
  .card-back {
    top: 470px;
    background: var(--brand-blue);
    display: flex;
    align-items: center;
    justify-content: center;
  }
  .brand-name {
    font-family: "Montserrat", sans-serif;
    font-weight: 800;
    color: var(--brand-blue);
    margin: 0;
    white-space: nowrap;
    line-height: 1;
  }
  .brand-name--top {
    position: absolute;
    left: 22px;
    top: 58px;
    font-size: 33px;
    letter-spacing: 1px;
  }
  .brand-name--decor {
    position: absolute;
    right: 23px;
    top: 240px;
    font-size: 33px;
    letter-spacing: 1px;
  }
  .brand-name--back {
    color: var(--text-light);
    font-size: 60px;
    letter-spacing: 3px;
  }
  .holder {
    position: absolute;
    right: 22px;
    top: 50px;
    text-align: right;
  }
  .holder-name {
    font-family: "Montserrat", sans-serif;
    font-weight: 700;
    font-size: 20px;
    color: var(--brand-blue);
    margin: 0;
    line-height: 1.1;
  }
  .holder-title {
    font-family: "Montserrat", sans-serif;
    font-weight: 500;
    font-size: 14.5px;
    color: var(--text-light);
    margin: 4px 0 0;
  }
  .holder-accent {
    position: absolute;
    right: 0;
    top: 52px;
    width: 9px;
    height: 39px;
    background: var(--brand-blue);
  }
  .contact {
    position: absolute;
    left: 22px;
    top: 173px;
    font-family: "Open Sans", sans-serif;
    font-size: 15.5px;
    color: var(--text-light);
  }
  .address {
    margin: 0 0 24px;
    line-height: 22px;
  }
  .contact-list {
    list-style: none;
    margin: 0;
    padding: 0;
  }
  .contact-list li {
    display: flex;
    align-items: center;
    height: 22px;
  }
  .contact-list svg {
    width: 13px;
    height: 13px;
    margin-right: 7px;
    fill: var(--brand-blue);
  }
  .footer-band {
    position: absolute;
    bottom: 0;
    height: 14px;
    background: var(--brand-blue);
  }
  .footer-band--left { left: 0; width: 288px; }
  .footer-band--right { left: 295px; right: 0; }
</style>
</head>
<body>
<div class="canvas">
  <section class="card card-front">
    <p class="brand-name brand-name--top">TA BRAMLEY</p>

    <div class="holder">
      <p class="holder-name">MARCUS HALE</p>
      <p class="holder-title">Managing Director</p>
    </div>
    <div class="holder-accent"></div>

    <div class="contact">
      <p class="address">Your address,<br>City State, Zip 1234</p>
      <ul class="contact-list">
        <li>
          <svg viewBox="0 0 24 24" aria-hidden="true"><path d="M6.6 10.8c1.4 2.8 3.8 5.1 6.6 6.6l2.2-2.2c.3-.3.7-.4 1-.2 1.1.4 2.3.6 3.6.6.6 0 1 .4 1 1V20c0 .6-.4 1-1 1C10.6 21 3 13.4 3 4c0-.6.4-1 1-1h3.5c.6 0 1 .4 1 1 0 1.3.2 2.5.6 3.6.1.3 0 .7-.2 1L6.6 10.8z"/></svg>
          123 456 789
        </li>
        <li>
          <svg viewBox="0 0 24 24" aria-hidden="true"><path d="M2 5h20v14H2z" opacity="0.85"/><path d="M2 5l10 8 10-8" fill="none" stroke="#161616" stroke-width="2"/></svg>
          info@youremail.com
        </li>
        <li>
          <svg viewBox="0 0 24 24" aria-hidden="true"><circle cx="12" cy="12" r="10"/><path d="M2 12h20M12 2c3 3 3 17 0 20M12 2c-3 3-3 17 0 20" fill="none" stroke="#161616" stroke-width="1.5"/></svg>
          www.yourwebsite.com
        </li>
      </ul>
    </div>

    <p class="brand-name brand-name--decor">TA BRAMLEY</p>

    <div class="footer-band footer-band--left"></div>
    <div class="footer-band footer-band--right"></div>
  </section>

  <section class="card card-back">
    <p class="brand-name brand-name--back">TA BRAMLEY</p>
  </section>
</div>
</body>
</html>
```